sydney wedding photography business needs a business card design

we need a business card design for a sydney based wedding photography and videography business. our business name is :golden hour studio and film. our target clients are 24-35 yrs female. our style is candid, organic, natural, dynamic. we are a team of young photographers and videographers, and help brides to create memories that they will cherish for the rest of their lives. the logo will be provided. we want an elegant design that reflects our style, and also want to give a great impression to our clients that we are one of the best studios in sydney and our brand means quality and premium service.

Target Market(s)

bride to be, 24-35 years old, living in sydney and surrunding areas

Industry/Entity Type

Wedding Photography

Contact Information for Business Card

address: 57 tarrant street, glenmore nsw 2047
mobile: 0431872259
phone: (02) 9163 2408
info@tidewillowstudio.net.au
www.tidewillowstudio.net.au
facebook:tidewillowweddings
instagram:tidewillowweddings

Font styles to use
Serif
Sans Serif

Requirements
Nice to have
• maybe add my slogan"memories beyond eternity" if the layout looks good
Should not have
• no black color, not good idea for wedding biz card

```html
<!DOCTYPE html>
<html lang="en">
<head>
<meta charset="utf-8">
<title>Golden Hour Studio and Film – Business Card</title>
<link rel="stylesheet" href="https://fonts.googleapis.com/css2?family=Source+Sans+3:wght@400;600&family=Oswald:wght@500&display=swap">
<style>
  :root {
    --page: #ffffff;
    --card-blue: #1c3d6a;
    --panel-navy: #0d1f35;
    --gold: #d6a02a;
    --gold-light: #f0c24a;
    --art-deep: #0a1320;
    --art-mid: #163763;
  }
  * { box-sizing: border-box; margin: 0; padding: 0; }
  html, body { width: 1200px; height: 1200px; overflow: hidden; background: var(--page); }
  body { position: relative; font-family: "Source Sans 3", sans-serif; color: var(--gold); }

  .card {
    position: absolute; left: 168px; width: 829px; height: 472px;
    background: var(--card-blue); overflow: hidden;
  }
  .card--front { top: 72px; }
  .card--back { top: 626px; }

  .lens-art {
    position: absolute; border-radius: 50%; z-index: 1;
    background: radial-gradient(circle at 50% 50%, var(--art-mid) 0%, var(--art-deep) 75%);
  }

  /* front */
  .front-band {
    position: absolute; left: 0; top: 327px; width: 360px; height: 65px;
    background: var(--panel-navy);
  }
  .card--front .lens-art { left: 257px; top: 80px; width: 316px; height: 316px; }
  .web-row {
    position: absolute; left: 10px; top: 352px; height: 22px; z-index: 2;
    display: flex; align-items: center; gap: 14px;
  }
  .dot { display: block; border-radius: 50%; background: var(--gold); }
  .web-url { font-size: 11.5px; color: var(--gold-light); margin: 0 10px; letter-spacing: .1px; }
  .brand-name {
    position: absolute; left: 255px; width: 320px; top: 200px; z-index: 2;
    text-align: center; font-weight: 600; color: var(--gold-light); line-height: 1;
  }
  .brand-name .line-1 { display: block; font-size: 40px; }
  .brand-name .line-2 { display: block; font-size: 14px; letter-spacing: 6px; margin-top: 14px; }

  /* back */
  .contact-panel {
    position: absolute; left: 0; top: 87px; width: 540px; height: 366px;
    background: var(--panel-navy);
  }
  .card--back .lens-art { left: 336px; top: 88px; width: 350px; height: 362px; }
  .person-name {
    position: absolute; left: 550px; top: 12px;
    font-family: "Oswald", sans-serif; font-weight: 500; font-size: 40px;
    letter-spacing: 14px; color: var(--gold); line-height: 1.2;
  }
  .person-role {
    position: absolute; left: 547px; top: 68px;
    font-size: 12px; letter-spacing: 3.4px; color: var(--gold);
  }
  .contact-icon { position: absolute; z-index: 2; }
  .contact-text {
    position: absolute; font-size: 18.5px; line-height: 24px; color: var(--gold-light);
    white-space: nowrap; z-index: 3;
  }
</style>
</head>
<body>

<section class="card card--front">
  <div class="front-band"></div>
  <div class="lens-art" role="img" aria-label="Illustration of a camera lens"></div>
  <div class="web-row">
    <span class="dot" style="width:3px;height:3px"></span>
    <span class="dot" style="width:4px;height:4px"></span>
    <span class="dot" style="width:6px;height:6px"></span>
    <span class="dot" style="width:7px;height:7px"></span>
    <span class="dot" style="width:8px;height:8px"></span>
    <span class="dot" style="width:10px;height:10px"></span>
    <span class="web-url">www.tidewillowstudio.net.au</span>
    <span class="dot" style="width:10px;height:10px"></span>
    <span class="dot" style="width:8px;height:8px"></span>
    <span class="dot" style="width:7px;height:7px"></span>
    <span class="dot" style="width:6px;height:6px"></span>
    <span class="dot" style="width:4px;height:4px"></span>
    <span class="dot" style="width:3px;height:3px"></span>
  </div>
  <h1 class="brand-name"><span class="line-1">golden hour</span><span class="line-2">STUDIO AND FILM</span></h1>
</section>

<section class="card card--back">
  <div class="contact-panel"></div>
  <div class="lens-art" role="img" aria-label="Illustration of a camera lens"></div>
  <h2 class="person-name">NAME</h2>
  <p class="person-role">PHOTOGRAPHER&amp;VEDIOGRAPHER</p>

  <svg class="contact-icon" style="left:33px;top:124px" width="30" height="42" viewBox="0 0 30 42" aria-hidden="true">
    <path d="M15 1C7 1 1 7 1 15c0 10 14 26 14 26s14-16 14-26C29 7 23 1 15 1z" fill="var(--gold)"/>
    <circle cx="15" cy="15" r="6" fill="var(--panel-navy)"/>
  </svg>
  <p class="contact-text" style="left:115px;top:126px">57 tarrant street,<br>&nbsp;glenmore nsw 2047.</p>

  <svg class="contact-icon" style="left:37px;top:218px" width="36" height="38" viewBox="0 0 36 38" aria-hidden="true">
    <path d="M8 2l6 9-4 4c3 6 7 10 13 13l4-4 9 6-4 7C18 37 1 20 1 7z" fill="var(--gold)"/>
  </svg>
  <p class="contact-text" style="left:125px;top:222px">mobile: 0431872259<br>phone: (02) 9163 2408</p>

  <svg class="contact-icon" style="left:39px;top:302px" width="34" height="24" viewBox="0 0 34 24" aria-hidden="true">
    <rect x="1" y="1" width="32" height="22" fill="var(--gold)"/>
    <path d="M1 1l16 12L33 1M1 23l12-11M33 23L21 12" stroke="var(--panel-navy)" stroke-width="2" fill="none"/>
  </svg>
  <p class="contact-text" style="left:137px;top:306px">info@tidewillowstudio.net.au</p>

  <svg class="contact-icon" style="left:48px;top:377px" width="38" height="38" viewBox="0 0 38 38" aria-hidden="true">
    <circle cx="19" cy="19" r="17" fill="var(--gold)"/>
    <g stroke="var(--panel-navy)" stroke-width="2" fill="none">
      <ellipse cx="19" cy="19" rx="7" ry="17"/>
      <path d="M2 19h34M5 10h28M5 28h28M19 2v34"/>
    </g>
  </svg>
  <p class="contact-text" style="left:138px;top:366px">facebook:tidewillowweddings<br>instagram:tidewillowweddings</p>
</section>

</body>
</html>
```